Brightway Haus Inc. Business Card Design

Brightway Haus Inc. is in search of a great clean design for our business cards!

Looking to incorporate our full logo and watermark on side one (however, I am open to having the text and watermark separated within the design.)

On side two, I am looking to have contact information (Name, Position, Phone #, Email, Website (www.thebrightwayhaus.ca). Can have the logo and/or watermark as part of the design if applicable.

Please add tagline "Where Shine Counts" on either side 1 or 2. This tagline can be in a sans serif, serif or cursive font as long as it compliments overall design. Capitalization can be title or sentence case depending on how it fits within the design.

Get creative!! Looking for a clean, crisp, premium design! Looking for a glossy card finish with spot UV features when printed. Cards will also be printed with rounded corners. Standard dimensions (3.5 x 2).

Target Market(s)

B2B - primary clients are business owners or property management corporations. (residential jobs are few and far between)

Industry/Entity Type

Business

Contact Information for Business Card

- clean, crisp design
- double sided
- spot UV accents and glossy finish upon printing
- standard business card size (3.5 x 2) with rounded corners
- please see project description for requirements per side

Font styles to use
Sans Serif

Requirements
Must have
• - adequate bleeds with print ready files
• - cohesive design elements between side 1 & 2
• - spot UV elements (can be on both sides or just one, use your discretion)
• - colour pallet should match the logo file provided
• - incorporate tagline "where shine counts" (this tagline can be in a serif or sans serif font as long as it is complimentary to the overall design.
Nice to have
• - Premium elements with a clean design
Should not have
• - Please omit cartoon or whimsical like designs, think premium.
• - Colours should not stray from the pallet of the provided logo.

```html
<!DOCTYPE html>
<html lang="en">
<head>
<meta charset="utf-8">
<title>Brightway Haus Inc. Business Cards</title>
<link rel="stylesheet" href="https://fonts.googleapis.com/css2?family=Roboto:wght@400;500;700&display=swap">
<style>
  :root {
    --backdrop: #4a423d;
    --card: #1b1e22;
    --teal: #1fb8b8;
    --navy: #34479a;
    --white: #f1f3f4;
    --silver: #cfd2d6;
    --rule: #6b7076;
  }
  * { margin: 0; padding: 0; box-sizing: border-box; }
  html, body {
    width: 1200px; height: 769px; overflow: hidden;
    background: var(--backdrop);
    font-family: "Roboto", sans-serif;
  }
  .sheet {
    position: relative; width: 1200px; height: 769px;
    display: flex; align-items: center; justify-content: center; gap: 40px;
  }
  .card {
    position: relative; width: 520px; height: 297px;
    background: var(--card); border-radius: 12px;
    box-shadow: 0 14px 30px rgba(0,0,0,.45);
  }
  /* Contact side */
  .contact .brand {
    position: absolute; top: 72px; left: 0; right: 0;
    display: flex; align-items: center; justify-content: center; gap: 10px;
  }
  .brand-square { width: 28px; height: 28px; background: var(--teal); }
  .contact .brand-name {
    font-weight: 700; font-size: 30px; letter-spacing: .5px; color: var(--teal);
  }
  .details {
    position: absolute; top: 150px; left: 0; right: 0;
    display: flex; justify-content: center; gap: 22px;
  }
  .person { text-align: right; color: var(--white); font-size: 13px; line-height: 1.35; }
  .person-name { color: var(--teal); font-weight: 700; font-size: 17px; }
  .person-role { color: var(--navy); font-weight: 500; font-size: 13px; letter-spacing: .5px; margin-bottom: 4px; }
  .person-site { font-size: 13px; }
  .divider { width: 1px; background: var(--rule); }
  .lines { list-style: none; color: var(--white); font-size: 13px; line-height: 1.5; }
  .lines li { display: flex; align-items: center; gap: 8px; white-space: nowrap; }
  .lines svg { width: 12px; height: 12px; flex: none; }
  /* Logo side */
  .logo-side .brand {
    position: absolute; top: 104px; left: 0; right: 0;
    display: flex; align-items: center; justify-content: center; gap: 12px;
  }
  .logo-side .brand-square { width: 32px; height: 32px; background: var(--silver); }
  .logo-side .brand-name {
    font-weight: 700; font-size: 32px; letter-spacing: .5px; color: var(--silver);
  }
  .tagline {
    position: absolute; top: 166px; left: 0; right: 0;
    display: flex; align-items: center; justify-content: center; gap: 8px;
    color: var(--white); font-size: 14px;
  }
  .tagline .rule { height: 1px; width: 110px; background: linear-gradient(90deg, transparent, var(--silver)); }
  .tagline .rule.end { background: linear-gradient(90deg, var(--silver), transparent); }
</style>
</head>
<body>
<main class="sheet">
  <section class="card contact">
    <div class="brand">
      <span class="brand-square"></span>
      <span class="brand-name">BRIGHTWAY HAUS INC.</span>
    </div>
    <div class="details">
      <div class="person">
        <p class="person-name">DANA WHITLOCK</p>
        <p class="person-role">CEO/FOUNDER</p>
        <p class="person-site">www.thebrightwayhaus.ca</p>
      </div>
      <div class="divider"></div>
      <ul class="lines">
        <li><svg viewBox="0 0 12 12"><path d="M2 1h3l1 3-2 1a7 7 0 0 0 3 3l1-2 3 1v3c-6 0-10-4-10-10z" fill="var(--teal)"/></svg>555 210 4837</li>
        <li><svg viewBox="0 0 12 12"><rect x="3" y="1" width="6" height="10" rx="1" fill="none" stroke="var(--white)" stroke-width="1.2"/></svg>555 318 6294</li>
        <li><svg viewBox="0 0 12 12"><rect x="1" y="4" width="10" height="7" rx="1" fill="var(--white)"/><rect x="4" y="2" width="4" height="2" fill="none" stroke="var(--white)"/></svg>555 472 9150</li>
        <li><svg viewBox="0 0 12 12"><path d="M1 6l3 3 7-7" fill="none" stroke="var(--teal)" stroke-width="2"/></svg>dana@thebrightwayhaus.ca</li>
      </ul>
    </div>
  </section>
  <section class="card logo-side">
    <div class="brand">
      <span class="brand-square"></span>
      <span class="brand-name">BRIGHTWAY HAUS INC.</span>
    </div>
    <p class="tagline"><span class="rule"></span>Where Shine Counts<span class="rule end"></span></p>
  </section>
</main>
</body>
</html>
```